"Career in Gradvel" | Poster design

We need a "We are hiring" poster design. We are a construction company based in Croatia and we are looking for 3 categories of construction workers. We want moder, serious and powerful poster . In attachment you can find our logo. The font of a text that is used in logo design is "nexa bold".

At the bottom (or where designer can see it) will be description of general condition. The poster must be simple and clear.

Target Market(s)

Wide range of employment

Industry/Entity Type

Construction Company

Colors

Designer to choose colors to be used in the design.

Requirements
Must have
• The text in poster that will be needed is "Mason/carpenter job", "Steel-bender job" and "Auxiliary worker". This terms may be wrong, but it will be translated in local language. Under all of them will be a short descrtiption row, and one row of salary. This is for all three categories.
• At the bottom (or where designer can see it) will be description of general condition. The poster must be simple and clear.

```html
<!DOCTYPE html>
<html lang="en">
<head>
<meta charset="utf-8">
<title>Career in Gradvel – We Are Hiring</title>
<link rel="stylesheet" href="https://fonts.googleapis.com/css2?family=Bebas+Neue&family=Roboto:wght@400;700&display=swap">
<style>
  :root {
    --page-grey: #ebebeb;
    --frame-grey: #6f6f6f;
    --amber-deep: #f8a51b;
    --amber: #fbb41d;
    --amber-light: #ffd23c;
    --ink: #2e2c2b;
    --white: #ffffff;
    --sky: #0fb7e3;
    --tangerine: #ec9217;
    --lime: #95c12b;
  }
  * { margin: 0; padding: 0; box-sizing: border-box; }
  html, body {
    width: 847px; height: 1200px; overflow: hidden;
    background: var(--page-grey);
  }
  .poster {
    position: absolute; left: 45px; top: 63px;
    width: 757px; height: 1073px;
    border: 1px solid var(--frame-grey);
    overflow: hidden;
    background: linear-gradient(115deg, var(--amber-deep) 0%, var(--amber) 45%, var(--amber-light) 75%, var(--amber) 100%);
  }
  .layer { position: absolute; left: -45px; top: -63px; width: 847px; height: 1200px; }

  .brand { position: absolute; left: 0; width: 847px; text-align: center; color: var(--white); }
  .brand-square {
    position: absolute; left: 386px; top: 125px; width: 72px; height: 72px;
    border: 3px solid var(--white);
  }
  .brand-name {
    top: 204px; font-family: "Roboto", sans-serif; font-weight: 400;
    font-size: 31px; letter-spacing: 3px; line-height: 32px;
  }
  .brand-tagline {
    top: 236px; font-family: "Roboto", sans-serif; font-weight: 400;
    font-size: 8.5px; letter-spacing: 0.3px;
  }

  .headline {
    position: absolute; left: 0; width: 847px; text-align: center;
    font-family: "Bebas Neue", sans-serif; color: var(--ink);
    line-height: 1; font-weight: 400;
  }
  .headline-top { top: 266px; font-size: 132px; letter-spacing: 2px; }
  .headline-main { top: 369px; font-size: 214px; letter-spacing: 4px; }

  .job {
    position: absolute; left: 201px; width: 445px; height: 126px;
    color: var(--white); text-align: center;
  }
  .job--mason { top: 575px; background: var(--sky); }
  .job--steel { top: 706px; background: var(--tangerine); height: 127px; }
  .job--aux { top: 839px; background: var(--lime); height: 127px; }
  .job-title {
    font-family: "Bebas Neue", sans-serif; font-size: 38px; font-weight: 400;
    letter-spacing: 0.5px; line-height: 36px; padding-top: 15px;
  }
  .job-text {
    font-family: "Roboto", sans-serif; font-weight: 700;
    font-size: 17.5px; line-height: 22px;
  }
  .divider {
    position: absolute; left: 177px; width: 493px; height: 2px;
    background: var(--white);
  }

  .contact {
    position: absolute; left: 0; top: 1003px; width: 847px; text-align: center;
    font-family: "Bebas Neue", sans-serif; font-size: 41px; color: var(--ink);
    letter-spacing: 0.5px; line-height: 40px; white-space: nowrap;
  }
  .contact-icon { display: inline-block; width: 34px; height: 26px; vertical-align: -2px; }
  .terms {
    position: absolute; left: 76px; top: 1060px; width: 698px;
    font-family: "Roboto", sans-serif; font-size: 11.6px; line-height: 15px;
    color: var(--ink); letter-spacing: -0.2px;
  }
</style>
</head>
<body>
<main class="poster">
  <div class="layer">
    <span class="brand-square" aria-hidden="true"></span>
    <p class="brand brand-name">GRADVEL</p>
    <p class="brand brand-tagline">IZVOĐENJE I VOĐENJE GRAĐEVINSKIH RADOVA</p>

    <h1>
      <span class="headline headline-top">We are</span>
      <span class="headline headline-main">Hiring</span>
    </h1>

    <section class="job job--mason">
      <h2 class="job-title">Mason/Carpenter job</h2>
      <p class="job-text">of them of them Under all of theof them<br>m will be a short descrtiption row<br>Sallery $85000</p>
    </section>
    <div class="divider" style="top:701px"></div>
    <section class="job job--steel">
      <h2 class="job-title">Steel-Bender job</h2>
      <p class="job-text">of them of them Under all of theof them<br>m will be a short descrtiption row<br>Sallery $85000</p>
    </section>
    <div class="divider" style="top:835px"></div>
    <section class="job job--aux">
      <h2 class="job-title">Auxiliary worker</h2>
      <p class="job-text">of them of them Under all of theof them<br>m will be a short descrtiption row<br>Sallery $85000</p>
    </section>

    <p class="contact">
      <svg class="contact-icon" viewBox="0 0 36 28" aria-label="Phone">
        <path d="M2 9 C8 1 28 1 34 9 L30 13 L25 10 L25 6 C20 4 16 4 11 6 L11 10 L6 13 Z" fill="#2e2c2b"/>
        <path d="M9 13 L13 9 L23 9 L27 13 L30 26 L6 26 Z" fill="#2e2c2b"/>
        <circle cx="18" cy="18" r="4" fill="#fbb41d"/>
      </svg>:10987654321 | Email: jobs@gradvel.com
    </p>
    <p class="terms">Terms &amp; Condations: is simply dummy text of the printing and typesetting industry. Lorem Ipsum has been the industry's standard dummy text ever since the 1500s, when an unknown printer took a galley of type and scrambled it to make a type specimen book. It has survived not only five centuries, but, remaining essentially unchanged.</p>
  </div>
</main>
</body>
</html>
```